Coastline Premier Retreats Business Card Design

Design a business card for Coastline Premier Retreats. Look at the website for colors and reference. Card should have logo, name, title, office number, mobile number, email, URL and a tagline like, "Luxury Hotel & Resort Email Marketing" (This might change).

https://www.coastlinepremierretreats.example

The rest I will leave up to your imagination.

Contact Information for Business Card

Logo, name, title, office number, mobile number, email, URL and a tagline like, "Luxury Hotel & Resort Email Marketing" (This might change).

```html
<!DOCTYPE html>
<html lang="en">
<head>
<meta charset="utf-8">
<title>Coastline Premier Retreats – Business Card</title>
<link rel="stylesheet" href="https://fonts.googleapis.com/css2?family=Open+Sans:wght@400;600;700;800&display=swap">
<style>
  :root {
    --backdrop: #232323;
    --card: #fffef3;
    --ink: #111111;
    --accent: #f07521;
    --rule: #2a2a2a;
  }
  * { box-sizing: border-box; margin: 0; padding: 0; }
  html, body {
    width: 1200px; height: 780px; overflow: hidden;
    background: var(--backdrop);
    font-family: "Open Sans", Arial, sans-serif;
    color: var(--ink);
  }
  .sheet {
    width: 1200px; height: 780px;
    display: flex; align-items: center; justify-content: center; gap: 30px;
  }
  .card {
    position: relative;
    width: 560px; height: 320px;
    background: var(--card);
    border-radius: 22px;
    overflow: hidden;
    box-shadow: 0 14px 30px rgba(0,0,0,.55);
  }
  .card-bands {
    position: absolute; left: 0; bottom: 0;
    width: 560px; height: 44px;
  }
  .band-accent { fill: var(--accent); }
  .band-dark { fill: var(--ink); }

  /* front */
  .front-brand {
    position: absolute; left: 0; right: 0; top: 96px;
    text-align: center;
  }
  .brand-name {
    font-weight: 800; text-transform: uppercase; color: var(--ink);
    letter-spacing: 1.5px; line-height: 1.1;
  }
  .front-brand .brand-name { font-size: 34px; }

  /* back */
  .back-brand {
    position: absolute; left: 28px; top: 128px; width: 210px;
    text-align: center;
  }
  .back-brand .brand-name { font-size: 18px; }
  .divider {
    position: absolute; left: 256px; top: 70px;
    width: 1px; height: 170px; background: var(--rule);
  }
  .contact {
    position: absolute; left: 282px; top: 58px; width: 270px;
  }
  .person-name { font-size: 27px; font-weight: 700; line-height: 1.1; }
  .person-first { color: var(--accent); }
  .person-role { font-size: 13px; font-weight: 600; margin-top: 2px; }
  .contact-list { list-style: none; margin-top: 14px; }
  .contact-item {
    display: flex; align-items: center; gap: 8px;
    font-size: 11.5px; line-height: 1.75;
  }
  .contact-icon { width: 13px; height: 13px; flex: none; }
  .contact-icon * { fill: none; stroke: var(--accent); stroke-width: 1.6; }
  .tagline {
    position: absolute; left: 248px; top: 244px;
    font-size: 15px; color: var(--accent);
  }
</style>
</head>
<body>
<main class="sheet">

  <section class="card card-front" aria-label="Card front">
    <div class="front-brand">
      <p class="brand-name">Coastline Premier<br>Retreats</p>
    </div>
    <svg class="card-bands" viewBox="0 0 560 44" aria-hidden="true">
      <polygon class="band-dark" points="348,4 560,4 560,44 318,44 342,16"/>
      <polygon class="band-accent" points="0,30 320,14 296,44 0,44"/>
    </svg>
  </section>

  <section class="card card-back" aria-label="Card back">
    <div class="back-brand">
      <p class="brand-name">Coastline Premier<br>Retreats</p>
    </div>
    <div class="divider"></div>
    <div class="contact">
      <h1 class="person-name"><span class="person-first">Marta</span> Kovalenko</h1>
      <p class="person-role">Managing Director</p>
      <ul class="contact-list">
        <li class="contact-item">
          <svg class="contact-icon" viewBox="0 0 14 14" aria-hidden="true"><path d="M3 1.5l2 2.5-1.2 1.4c.8 1.7 2 2.9 3.8 3.8L9 8l2.5 2-1.2 2C6 11.8 2.2 8 1.5 3.5z"/></svg>
          (555) 014-2758
        </li>
        <li class="contact-item">
          <svg class="contact-icon" viewBox="0 0 14 14" aria-hidden="true"><rect x="3.5" y="1" width="7" height="12" rx="1.2"/></svg>
          (555) 019-7777
        </li>
        <li class="contact-item">
          <svg class="contact-icon" viewBox="0 0 14 14" aria-hidden="true"><circle cx="7" cy="7" r="5.6"/><path d="M1.4 7h11.2M7 1.4c-2.4 3-2.4 8.2 0 11.2M7 1.4c2.4 3 2.4 8.2 0 11.2"/></svg>
          www.coastlinepremierretreats.example
        </li>
        <li class="contact-item">
          <svg class="contact-icon" viewBox="0 0 14 14" aria-hidden="true"><rect x="1" y="3" width="12" height="8.5" rx="1"/><path d="M1 3.5l6 4.5 6-4.5"/></svg>
          info@coastlinepremierretreats.example
        </li>
      </ul>
    </div>
    <p class="tagline">Luxury Hotel &amp; Resort Email Marketing</p>
    <svg class="card-bands" viewBox="0 0 560 44" aria-hidden="true">
      <polygon class="band-dark" points="348,4 560,4 560,44 318,44 342,16"/>
      <polygon class="band-accent" points="0,30 320,14 296,44 0,44"/>
    </svg>
  </section>

</main>
</body>
</html>
```